Counseling Practice Business Card

I need a professional looking business card incorporating my new logo that was just completed. Card needs to incorporate my name and title, description of my specialty, my address, my phone number, my fax number, my email and my website URL. I need to be able to choose design on/with different paper colors and textures.
I do not have a lot of business card ideas so I am open to anything but I want bold,sharp, clear card without additional designs other than my logo (see attached file info). I am open to different color backgrounds or paper colors including black. I do not like traditional brackets around area codes in phone number or dashes between numbers in phone number. Am open to other ways of presenting including periods between numbers as appropriate. I do not know enough to know what I like yet but I want card to coordinate and work together with my logo. My practice emphasizes natural mental health interventions so any use of color (with background paper color or the blue and green in my logo) that elicits nature is nice. In addition to black, any natural brown or wood looking background might be desirable also. Most of the offerings so far look very similar and boring.

Target Market(s)

Potential therapy clients and other professionals

Contact Information for Business Card

Card information:
Gerald M. Whitcombe, Ph.D.
Licensed Clinical Psychologist
Integrative Health Coach
4812 Marlowe Ridge Blvd SE
Suite 310
Duluth, GA 30096
(770) 415-2983 phone
(770) 581-4096 fax
drgeraldwhitcombe@quillmarsh.net
brightfernwellness.net

Font styles to use
Serif
Sans Serif
Other font styles liked:
• anything that you think looks crisp, clear and easily readable

Requirements
Must have
• Any color used should coordinate with my logo design (see attached files).
• Card should be printed horizontally so top and bottom are longest sides of rectangle.
• Background color or paper color should complement and highlight logo. Do not like a white background. black, grey, brown or any color my logo would blend well with.
Nice to have
• I would like designer to utilize color to highlight letters/name or phone-fax-web symbols.
• Bottom edge of card could be highlighted if appropriate to an idea.
Should not have
• I would NOT want the card to have a pure white background at all.
• No clear cards.
• Cards should be oriented with long sides on bottom and top, NOT sides. DO NOT LIKE THIS THIN TALL ORIENTATION.

```html
<!DOCTYPE html>
<html lang="en">
<head>
<meta charset="utf-8">
<title>Brightfern Wellness – Business Card</title>
<link href="https://fonts.googleapis.com/css2?family=Open+Sans:wght@400;600;700&display=swap" rel="stylesheet">
<style>
  :root {
    --stage: #2e2f31;
    --card: #111214;
    --blue: #2b7cc4;
    --navy: #0e2f52;
    --green: #1f7a3a;
    --text-light: #c9cbcf;
    --white: #ffffff;
    --divider: #3a3c40;
  }
  * { margin: 0; padding: 0; box-sizing: border-box; }
  html, body {
    width: 1200px; height: 840px; overflow: hidden;
    background: var(--stage);
    font-family: "Open Sans", sans-serif;
  }
  .canvas { position: relative; width: 1200px; height: 840px; }

  .card {
    position: absolute;
    width: 630px; height: 360px;
    background: var(--card);
    overflow: hidden;
    box-shadow: 0 10px 30px rgba(0,0,0,0.45);
  }
  .card--back { left: 150px; top: 40px; }
  .card--front { left: 420px; top: 440px; }

  /* Brand name lockup */
  .brand {
    display: flex; align-items: center; gap: 12px;
    color: var(--blue);
    font-weight: 600;
    line-height: 1;
    white-space: nowrap;
  }
  .brand__dot {
    width: 22px; height: 22px; border-radius: 50%;
    background: var(--green); flex: none;
  }

  /* Back side */
  .card--back .brand {
    position: absolute; left: 0; right: 0; top: 120px;
    justify-content: center;
    font-size: 44px;
  }
  .card--back .site {
    position: absolute; left: 0; right: 0; top: 250px;
    text-align: center;
    color: var(--text-light);
    font-size: 15px;
    letter-spacing: 5px;
  }

  /* Front side */
  .band { position: absolute; inset: 0; }
  .identity {
    position: absolute; right: 26px; top: 22px;
    text-align: right; line-height: 1.25;
  }
  .identity__name {
    color: var(--white); font-weight: 700; font-size: 21px;
    text-transform: uppercase; letter-spacing: 0.3px;
  }
  .identity__role { color: var(--navy); font-size: 15px; }

  .card--front .brand {
    position: absolute; left: 30px; top: 270px;
    gap: 9px;
    font-size: 23px;
  }
  .card--front .brand__dot { width: 15px; height: 15px; }

  .divider {
    position: absolute; left: 318px; top: 178px;
    width: 1px; height: 150px; background: var(--divider);
  }
  .contact {
    position: absolute; left: 338px; top: 182px;
    color: var(--text-light); font-size: 13.5px; line-height: 1.42;
    list-style: none;
  }
  .contact__address { margin-bottom: 2px; }
  .contact__item { display: flex; align-items: center; gap: 8px; }
  .contact__icon {
    width: 14px; height: 14px; flex: none;
    fill: var(--blue); stroke: var(--blue);
  }
</style>
</head>
<body>
<main class="canvas">

  <section class="card card--back" aria-label="Card back">
    <div class="brand"><span class="brand__dot"></span>Brightfern Wellness</div>
    <p class="site">www.brightfernwellness.net</p>
  </section>

  <section class="card card--front" aria-label="Card front">
    <svg class="band" width="630" height="360" viewBox="0 0 630 360" aria-hidden="true">
      <path d="M0,0 H630 V100 Q330,118 0,210 Z" fill="var(--blue)"/>
      <path d="M0,210 Q330,118 630,100 V112 Q330,132 0,222 Z" fill="var(--green)"/>
    </svg>

    <div class="identity">
      <p class="identity__name">Gerald M. Whitcombe, Ph.D.</p>
      <p class="identity__role">Licensed Clinical Psychologist</p>
      <p class="identity__role">Integrative Health Coach</p>
    </div>

    <div class="brand"><span class="brand__dot"></span>Brightfern Wellness</div>

    <div class="divider"></div>

    <ul class="contact">
      <li class="contact__address">4812 Marlowe Ridge Blvd SE<br>Suite 310<br>Duluth, GA 30096</li>
      <li class="contact__item">
        <svg class="contact__icon" viewBox="0 0 16 16" aria-hidden="true"><path stroke="none" d="M3 1h3l1.5 4-2 1.2a9 9 0 0 0 4.3 4.3L11 8.5l4 1.5v3a2 2 0 0 1-2 2A12 12 0 0 1 1 3a2 2 0 0 1 2-2z"/></svg>
        (770) 415-2983
      </li>
      <li class="contact__item">
        <svg class="contact__icon" viewBox="0 0 16 16" aria-hidden="true"><rect x="4" y="1" width="8" height="5" fill="none" stroke-width="1.5"/><rect x="1" y="6" width="14" height="7" rx="1" stroke="none"/><rect x="4" y="11" width="8" height="4" stroke="none"/></svg>
        (770) 581-4096
      </li>
      <li class="contact__item">
        <svg class="contact__icon" viewBox="0 0 16 16" aria-hidden="true"><rect x="1" y="3" width="14" height="10" rx="1" stroke="none"/><path d="M1.5 3.5 8 9l6.5-5.5" fill="none" stroke="var(--card)" stroke-width="1.4"/></svg>
        drgeraldwhitcombe@quillmarsh.net
      </li>
      <li class="contact__item">
        <svg class="contact__icon" viewBox="0 0 16 16" aria-hidden="true"><circle cx="8" cy="8" r="7" stroke="none"/><path d="M1 8h14M8 1c-3 3.5-3 10.5 0 14M8 1c3 3.5 3 10.5 0 14" fill="none" stroke="var(--card)" stroke-width="1"/></svg>
        www.brightfernwellness.net
      </li>
    </ul>
  </section>

</main>
</body>
</html>
```